Professional Package for CPA Firm

We would like a stationery design for our new CPA Firm based in Atlanta, GA called 'Vale 8'. We work with investors to help grow investments, tax free. We would like the design to have a professional/minimal look with a 'wow' factor. We need 9.5″ x 4.125″, 9x12, and 10x13 mailing envelopes, business cards, and a letterhead. We have a logo that is already complete. For the letterhead, we would like to have space to put credentials at the bottom of the page

Industry/Entity Type

CPA, Accounting

```html
<!DOCTYPE html>
<html lang="en">
<head>
<meta charset="utf-8">
<title>Vale 8 — Business Card</title>
<link rel="stylesheet" href="https://fonts.googleapis.com/css2?family=Open+Sans:wght@400;600&family=Montserrat:wght@600&display=swap">
<style>
  :root {
    --navy: #0d3350;
    --teal: #2ab3b1;
    --coral: #f05a5b;
    --paper: #ffffff;
    --backdrop: #e6e8ea;
    --ink-light: #ffffff;
  }
  * { box-sizing: border-box; margin: 0; padding: 0; }
  html, body { width: 1200px; height: 874px; overflow: hidden; }
  body {
    background: var(--backdrop);
    font-family: "Open Sans", sans-serif;
    position: relative;
  }
  .card {
    position: absolute;
    left: 320px;
    width: 560px;
    height: 320px;
    border-radius: 18px;
    overflow: hidden;
    background: var(--navy);
    box-shadow: 0 6px 18px rgba(0,0,0,0.18);
  }
  .card--front { top: 84px; }
  .card--back { top: 470px; }

  .brand {
    position: absolute;
    text-align: center;
  }
  .brand__name {
    font-family: "Montserrat", sans-serif;
    font-weight: 600;
    letter-spacing: 3px;
    line-height: 1;
  }
  .brand__tagline {
    margin-top: 8px;
    font-size: 13px;
    letter-spacing: 2.5px;
  }
  .card--front .brand {
    left: 0; right: 0; top: 112px;
  }
  .card--front .brand__name { font-size: 64px; color: var(--teal); }
  .card--front .brand__tagline { color: var(--teal); }

  .card__shape { position: absolute; inset: 0; }

  .card--back .brand {
    left: 300px; right: 20px; top: 146px;
  }
  .card--back .brand__name { font-size: 50px; color: var(--navy); }
  .card--back .brand__tagline { color: var(--navy); font-size: 11px; letter-spacing: 2px; }

  .contact {
    position: absolute;
    left: 36px;
    top: 64px;
    color: var(--ink-light);
  }
  .contact__name {
    font-size: 19px;
    font-weight: 600;
    color: var(--teal);
    letter-spacing: 0.5px;
    text-transform: uppercase;
  }
  .contact__role {
    font-size: 13px;
    color: var(--coral);
    margin-bottom: 12px;
  }
  .contact__address { font-size: 13px; line-height: 1.35; margin-bottom: 10px; }
  .contact__list { list-style: none; font-size: 13px; line-height: 1.4; }
  .contact__list li { display: flex; align-items: center; gap: 8px; }
  .contact__icon { width: 11px; height: 11px; flex: none; }
</style>
</head>
<body>

  <section class="card card--front" aria-label="Business card front">
    <div class="brand">
      <div class="brand__name">VALE 8</div>
      <div class="brand__tagline">CPAs and Tax Advisors</div>
    </div>
  </section>

  <section class="card card--back" aria-label="Business card back">
    <svg class="card__shape" viewBox="0 0 560 320" aria-hidden="true">
      <path d="M296 0 L268 150 Q262 185 262 215 L262 320 L560 320 L560 0 Z" fill="var(--teal)"/>
      <path d="M304 0 L276 150 Q270 185 270 215 L270 320 L560 320 L560 0 Z" fill="var(--coral)"/>
      <path d="M312 0 L284 150 Q278 185 278 215 L278 320 L560 320 L560 0 Z" fill="var(--paper)"/>
    </svg>

    <div class="contact">
      <div class="contact__name">Daniel Reyes</div>
      <div class="contact__role">President</div>
      <div class="contact__address">214 Birchwood Court<br>Atlanta, Georgia 30318</div>
      <ul class="contact__list">
        <li>
          <svg class="contact__icon" viewBox="0 0 12 12"><path d="M2.5 1 L4.5 1 L5.3 3.5 L4 4.6 Q5 7 7.4 8 L8.5 6.7 L11 7.5 L11 9.5 Q10.5 11 9 11 Q1 10 1 3 Q1 1.5 2.5 1 Z" fill="var(--coral)"/></svg>
          404-555-0142
        </li>
        <li>
          <svg class="contact__icon" viewBox="0 0 12 12"><rect x="3" y="0.8" width="6" height="10.4" rx="1" fill="none" stroke="var(--coral)" stroke-width="1.4"/></svg>
          404-555-0187
        </li>
        <li>
          <svg class="contact__icon" viewBox="0 0 12 12"><rect x="0.5" y="2" width="11" height="8" fill="var(--coral)"/><path d="M0.5 2 L6 6.5 L11.5 2" fill="none" stroke="var(--navy)" stroke-width="1"/></svg>
          info@vale8.com
        </li>
        <li>
          <svg class="contact__icon" viewBox="0 0 12 12"><circle cx="6" cy="6" r="5.3" fill="var(--coral)"/><path d="M1 6 H11 M6 0.8 Q3 6 6 11.2 M6 0.8 Q9 6 6 11.2" fill="none" stroke="var(--navy)" stroke-width="0.9"/></svg>
          www.vale8.com
        </li>
      </ul>
    </div>

    <div class="brand">
      <div class="brand__name">VALE 8</div>
      <div class="brand__tagline">CPAs and Tax Advisors</div>
    </div>
  </section>

</body>
</html>
```